Responsive Mobile Quelvo Jewelry Template

We need to adapt an existing Quelvo template to be 100% responsive and mobile friendly. Due to Quelvo rules, the template would need to be implemented only using HTML and CSS (no Javascript). The template design files and HTML/CSS files are required for this project. We prefer that it is implemented using a responsive framework such as Gridwell.

An example of our current template can be found here (diamond only):
https://www.quelvo-market.example/itm/507318829106?ViewItem=&item=507318829106

And example of our template with an additional section for gemstone:
https://www.quelvo-market.example/itm/507318826673?ViewItem=&item=507318826673

We had also somewhat recently designed our Quelvo store landing page so some consistency with this would be desired:
http://www.quelvoshops.example/MirrowCraftNV

Please also refer to our website: https://mirrowcraftnv.example/

Target Market(s)

Primarily women shopping for jewelry on Quelvo.

Industry/Entity Type

Jewelry

Coding

Coded - Design and coding required

Number of Pages Required

1 page

Font styles to use
Sans Serif

Requirements
Must have
• * A color scheme that fits with the existing template design.
• * REMOVE the product photo in the template.
• * Sections required for Description, Basic Details, and Diamond/Gemstone Details.
• * Please refer to https://pages.quelvo-market.example/sell/itemdescription/mobilefriendlyguidelines.html in particular, the template must use
Nice to have
• * Menu of links to other categories is desired in a mobile friendly way.
• * We are open to graphics for links to popular categories similar to those found on the store page.
• * Implemented using a standardized responsive framework such as Gridwell.

```html
<!DOCTYPE html>
<html lang="en">
<head>
<meta charset="utf-8">
<title>Mirrow Craft – Item Listing</title>
<link href="https://fonts.googleapis.com/css2?family=Poppins:wght@400;500;600&family=Roboto:wght@400;500&family=Roboto+Condensed:wght@400&family=Cormorant+Garamond:wght@500&display=swap" rel="stylesheet">
<style>
:root{
  --purple:#8464a3;
  --purple-light:#9a7fb8;
  --lavender:#d8c8f1;
  --page:#f3f3f3;
  --card:#ffffff;
  --text:#333333;
  --muted:#555555;
  --line:#e6e6e6;
  --border:#dcdcdc;
}
*{box-sizing:border-box;margin:0;padding:0}
html,body{width:973px;height:1200px;overflow:hidden}
body{background:var(--page);font-family:'Poppins',sans-serif;color:var(--text);position:relative}

.site-header{height:115px;background:linear-gradient(180deg,var(--lavender) 0%,#f1ebfb 70%,#fbf9fe 100%);display:flex;justify-content:center;align-items:center}
.brand{background:rgba(255,255,255,.55);width:342px;height:108px;display:flex;flex-direction:column;align-items:center;justify-content:center;gap:4px}
.brand-mark{width:26px;height:26px;border-radius:50%;background:var(--purple-light)}
.brand-name{font-family:'Cormorant Garamond',serif;font-weight:500;font-size:20px;color:var(--purple);letter-spacing:.5px}

.main-nav{height:39px;background:var(--purple);display:flex;justify-content:center;align-items:center;gap:27px}
.main-nav a{color:#fff;text-decoration:none;font-family:'Roboto',sans-serif;font-weight:500;font-size:12.5px;letter-spacing:.2px}

.card{position:absolute;background:var(--card);border:1px solid var(--border);box-shadow:0 1px 2px rgba(0,0,0,.06)}
.card-head{height:35px;background:var(--purple);color:#fff;display:flex;align-items:center;padding-left:14px;gap:10px;font-weight:600;font-size:15.5px}
.head-dot{width:16px;height:16px;border-radius:50%;border:2px solid #fff;flex:none}

.category-menu{left:63px;top:191px;width:255px}
.category-menu .card-head{height:50px;font-weight:400;font-size:11.5px;line-height:15px;padding-left:14px}
.category-menu .head-dot{width:26px;height:26px}
.category-menu ul{list-style:none}
.category-menu li{height:36.5px;border-top:1px solid var(--line);display:flex;align-items:center;padding-left:14px;gap:16px;font-size:11.5px;white-space:nowrap}
.cat-icon{width:20px;height:20px;border-radius:4px;background:#c9c9c9;flex:none}

.badge{left:63px;width:255px;display:flex;align-items:center;justify-content:center}
.badge-shape{background:#c6cbd2}
.badge-accred{top:637px;height:97px}
.badge-accred .badge-shape{width:40px;height:62px;border-radius:3px;background:#2f5d88}
.badge-inst{top:757px;height:89px}
.badge-inst .badge-shape{width:90px;height:50px;border-radius:4px;background:#b89c62}
.badge-lab{top:868px;height:101px}
.badge-lab .badge-shape{width:76px;height:76px;border-radius:50%;background:#5b7fa8}

.item-description{left:337px;top:191px;width:299px;height:231px}
.item-description .body{padding:20px 15px 0 15px;font-size:10.3px;line-height:18.5px;color:var(--muted)}
.item-description p+p{margin-top:8px}

.spec-table{width:100%;border-collapse:collapse;table-layout:fixed;font-size:9.8px}
.spec-table td{height:26.7px;border-bottom:1px solid var(--line);vertical-align:middle;color:var(--muted);white-space:nowrap}
.spec-table tr:last-child td{border-bottom:none}
.spec-table td:first-child{padding-left:13px;color:#444}
.spec-table .sep{text-align:center}

.diamond-details{left:337px;top:439px;width:299px;height:150px}
.diamond-details td:first-child{width:106px}.diamond-details .sep{width:26px}
.questions{left:337px;top:603px;width:299px;height:75px}
.questions .body{display:flex;align-items:center;gap:8px;padding:13px 14px;font-size:10px;color:var(--muted)}

.item-details{left:654px;top:191px;width:256px;height:212px}
.item-details .spec-table{font-size:9.6px}
.item-details td:first-child{width:82px}.item-details .sep{width:16px}
.gemstone-details{left:654px;top:422px;width:256px;height:257px}
.gemstone-details td:first-child{width:106px}.gemstone-details .sep{width:20px}
.natural-note{font-size:8.3px;padding:5px 13px;color:var(--muted)}
.natural-note b{color:var(--purple);font-weight:500}

.policy-tabs{left:337px;top:700px;width:571px;height:271px}
.tab-bar{display:flex;height:36px;background:var(--purple)}
.tab{color:#fff;font-family:'Roboto Condensed',sans-serif;font-size:11px;display:flex;align-items:center;justify-content:center;border-left:1px solid var(--purple-light);white-space:nowrap}
.tab.active{background:#fff;color:var(--purple);border-left:none;gap:8px}
.tab.active .head-dot{border-color:var(--purple);width:14px;height:14px}
.tab-body{padding:14px 17px 0 17px;font-size:9.6px;line-height:18.5px;color:var(--muted)}
.tab-body p{margin-bottom:6px}
.tab-body .lead{font-size:10.5px}
.tab-body h4{font-weight:500;font-size:11px;color:#222;margin-bottom:7px}

.site-footer{position:absolute;left:60px;top:1009px;width:848px;height:140px;background:#f6f6f6;border:1px solid var(--border);text-align:center}
.footer-links{margin-top:30px;font-size:11.5px;color:#444}
.footer-links span{margin:0 5px}
.copyright{margin-top:13px;font-size:12.5px;color:#444}
.social{display:flex;justify-content:center;gap:8px;margin-top:13px}
.social i{width:24px;height:24px;border-radius:50%;border:1px solid #9aa4b5;display:block}
</style>
</head>
<body>
<header class="site-header">
  <div class="brand">
    <span class="brand-mark"></span>
    <span class="brand-name">MIRROW CRAFT</span>
  </div>
</header>
<nav class="main-nav">
  <a href="#">HOME</a><a href="#">ABOUT US</a><a href="#">FAQS</a><a href="#">WHY BUY FROM US</a><a href="#">SAVE SELLER</a><a href="#">BLOG</a><a href="#">CONTACT US</a>
</nav>

<aside class="card category-menu">
  <div class="card-head"><span class="head-dot"></span><span>Please choose a category below<br>to see more subcategories</span></div>
  <ul>
    <li><span class="cat-icon" role="img" aria-label="Engagement ring icon"></span>Diamond Engagement Rings</li>
    <li><span class="cat-icon" role="img" aria-label="Diamond icon"></span>Fancy Yellow &amp; Pink Diamond</li>
    <li><span class="cat-icon" role="img" aria-label="Cocktail ring icon"></span>Cocktail Fashion Diamond Rings</li>
    <li><span class="cat-icon" role="img" aria-label="Gemstone ring icon"></span>Colored Gemstone Diamond Rings</li>
    <li><span class="cat-icon" role="img" aria-label="Semi mount ring icon"></span>Semi Mount Diamond Rings</li>
    <li><span class="cat-icon" role="img" aria-label="Men's jewelry icon"></span>Men's Diamond Jewelry</li>
    <li><span class="cat-icon" role="img" aria-label="Pendant icon"></span>Diamond Pendants</li>
    <li><span class="cat-icon" role="img" aria-label="Earrings icon"></span>Diamond Earrings</li>
    <li><span class="cat-icon" role="img" aria-label="Necklace icon"></span>Diamond Necklaces</li>
    <li><span class="cat-icon" role="img" aria-label="Bracelet icon"></span>Diamond Bracelets &amp; Bangles</li>
  </ul>
</aside>

<div class="card badge badge-accred"><span class="badge-shape" role="img" aria-label="Accreditation badge"></span></div>
<div class="card badge badge-inst"><span class="badge-shape" role="img" aria-label="Gemological institute badge"></span></div>
<div class="card badge badge-lab"><span class="badge-shape" role="img" aria-label="Gemological laboratory seal"></span></div>

<section class="card item-description">
  <div class="card-head"><span class="head-dot"></span>Item Description</div>
  <div class="body">
    <p>Elegant 6mm Asscher Cut Peridot Gemstone Beautifully Mounted In A Classic 14k White Gold Setting Highlighted By Brilliant Cut Diamonds</p>
    <p>Sed ut perspiciatis unde omnis iste natus error sit voluptatem accusantium doloremque laudantium, totam rem aperiam, eaque ipsa quae ab illo inventore veritatis et quasi architecto beatae vitae dicta sunt explicabo. quae ab illo</p>
  </div>
</section>

<section class="card diamond-details">
  <div class="card-head"><span class="head-dot"></span>Diamond Details</div>
  <table class="spec-table">
    <tr><td>Total Carat Weight</td><td class="sep">:</td><td>0.33 CT</td></tr>
    <tr><td>Diamond Count</td><td class="sep">:</td><td>46</td></tr>
    <tr><td>Shape</td><td class="sep">:</td><td>Round</td></tr>
    <tr><td>Color/Clarity</td><td class="sep">:</td><td>G / VSI</td></tr>
  </table>
</section>

<section class="card questions">
  <div class="card-head"><span class="head-dot"></span>Questions?</div>
  <div class="body">
    <svg width="11" height="9" viewBox="0 0 11 9"><rect x=".6" y=".6" width="9.8" height="7.8" fill="none" stroke="#333" stroke-width="1.2"/><path d="M.6 .6 5.5 4.8 10.4 .6" fill="none" stroke="#333" stroke-width="1.2"/></svg>
    Ask a question via email
  </div>
</section>

<section class="card item-details">
  <div class="card-head"><span class="head-dot"></span>Item Details</div>
  <table class="spec-table">
    <tr><td>Model Number</td><td class="sep">:</td><td>MCN-RG40527PD-WT</td></tr>
    <tr><td>Metal</td><td class="sep">:</td><td>14k White Gold</td></tr>
    <tr><td>Weight</td><td class="sep">:</td><td>3.72 grams</td></tr>
    <tr><td>L x W x H</td><td class="sep">:</td><td>6 x 21.4 x 7.6 MM</td></tr>
    <tr><td>Style</td><td class="sep">:</td><td>Solitaire with Accents</td></tr>
    <tr><td>Ring Size</td><td class="sep">:</td><td>7 (contact us for sizing options)</td></tr>
  </table>
</section>

<section class="card gemstone-details">
  <div class="card-head"><span class="head-dot"></span>Gemstone Details</div>
  <table class="spec-table">
    <tr><td>Total Carat Weight</td><td class="sep">:</td><td>1.00 CT</td></tr>
    <tr><td>Gemstone Count</td><td class="sep">:</td><td>1</td></tr>
    <tr><td>Main Stone</td><td class="sep">:</td><td>Peridot</td></tr>
    <tr><td>Shape</td><td class="sep">:</td><td>Asscher</td></tr>
    <tr><td>Color</td><td class="sep">:</td><td>Green-Yellow</td></tr>
    <tr><td>Treatment</td><td class="sep">:</td><td>Oiled</td></tr>
    <tr><td>Certificate</td><td class="sep">:</td><td>VGL (click for more info)</td></tr>
  </table>
  <p class="natural-note">All of our <b>diamonds</b> and <b>gemstones</b> are <b>100% natural!</b></p>
</section>

<section class="card policy-tabs">
  <div class="tab-bar">
    <div class="tab active" style="width:151px"><span class="head-dot"></span>SHIPPING DETAILS</div>
    <div class="tab" style="width:140px">PRODUCT GUARANTEE</div>
    <div class="tab" style="width:104px">RETURN POLICY</div>
    <div class="tab" style="width:107px">PRIVACY POLICY</div>
    <div class="tab" style="width:69px">WHY US</div>
  </div>
  <div class="tab-body">
    <p class="lead">Parcelwing 2 Day: Free (U.S.A. only)</p>
    <h4>WE SHIP WORLDWIDE</h4>
    <p>International Buyers - Please Note: Import duties, taxes, and charges are not included in the item price or shipping cost. These charges are the buyer's responsibility. Please check with your country's customs office to determine what these additional costs will be prior to bidding or buying.</p>
    <p>All packages are fully insured and require signature confirmation.</p>
    <p>Once your item(s) are ready to leave our facility a shipping tracking number will be sent to you. Business days do not include Saturday, Sunday or holidays. Please be sure to inspect your package upon arrival for tampering or any damage. Rush orders are welcome. Please call for availability.</p>
  </div>
</section>

<footer class="site-footer">
  <div class="footer-links">Sitemap<span>|</span>Privacy Policy<span>|</span>Cookie Policy<span>|</span>Terms and Conditions</div>
  <div class="copyright">Mirrow Craft © 2018 All Rights Reserved.</div>
  <div class="social"><i></i><i></i><i></i></div>
</footer>
</body>
</html>
```